velorahelp Web Design Project

It is a virtual assistance/concierge company that helps the busy professional by remotely providing administrative, technical and/or creative business support services, specializing in the medical device industry. Company name is velorahelp.
(website will be velorahelp.example)

Allowing things to be done without taking time away from more urgent issues or family/personal time. Partnering with a VA reduces stress, protects cash flow, eliminates administrative hassles, and enables business people to find the success they originally set out to achieve. Saves small businesses and/or individuals on overhead, salary, et. Work is done remotely to offer administrative, clerical, typing and specialist service assistance on a regular, ad-hoc or emergency cover basis.

Though we are capable of addressing the needs of medical professionals and industry representatives due to our experience and knowledge (sales, HCC guidelines, etc.) we do not want to be limited to that market only.

Target Market(s)

Target market would be M/F, 30-50, National, busy, Alpha, entrepreneurs and industry professionals who want/need to do more without sacrifice of life

Requirements
Nice to have
• We do have a logo designed via the PlanMarket website that can/should be included. Logo is uploaded.

```html
<!DOCTYPE html>
<html lang="en">
<head>
<meta charset="utf-8">
<title>velorahelp</title>
<link rel="stylesheet" href="https://fonts.googleapis.com/css2?family=Open+Sans:ital,wght@0,400;0,600;0,700;1,700&family=Tinos:ital,wght@0,400;1,400;1,700&display=swap">
<style>
:root{
  --ink:#333;
  --muted:#666;
  --faint:#999;
  --blue:#2a7cc0;
  --line:#d4d4d4;
  --paper:#fff;
  --foot:#f6f6f6;
}
*{box-sizing:border-box;margin:0;padding:0}
html,body{width:722px;height:1200px;overflow:hidden;background:var(--paper)}
body{position:relative;font-family:"Open Sans",Verdana,sans-serif;color:var(--ink)}
.abs{position:absolute}

/* header */
.brand{left:75px;top:34px;font-size:28px;font-weight:400;color:var(--ink);line-height:1}
.call{right:70px;top:27px;font-size:12px;color:var(--muted)}
.search{left:518px;top:52px;width:134px;height:23px;border:1px solid #bbb;border-radius:3px;font-size:11px;color:var(--muted);padding:3px 6px}
.search svg{position:absolute;right:6px;top:5px}

/* nav */
.nav{left:72px;top:92px;width:581px;height:48px;border:1px solid var(--line);border-radius:4px;box-shadow:0 1px 2px rgba(0,0,0,.08)}
.nav span{position:absolute;top:15px;font-size:13px;color:var(--ink)}
.nav .current{text-decoration:underline}

/* hero */
.hero{left:73px;top:152px;width:580px;height:242px;background:linear-gradient(120deg,#9fb8c2 0%,#e6eef1 45%,#f3f3f3 70%,#c8ced2 100%);box-shadow:0 2px 5px rgba(0,0,0,.35)}
.dots{left:345px;top:406px;display:flex;gap:3px}
.dots i{width:8px;height:8px;border-radius:50%;background:#999}
.dots i:first-child{background:var(--blue)}

/* features */
.feature{top:451px;width:182px}
.feature h3{font-family:Tinos,Georgia,serif;font-style:italic;font-weight:700;font-size:13px;text-align:center;color:#222;height:31px}
.feature .photo{width:180px;height:105px;border:1px solid #ccc;box-shadow:0 1px 3px rgba(0,0,0,.25)}
.feature p{margin-top:18px;width:188px;font-size:12px;line-height:16px;padding-left:1px}
.btn{display:block;width:51px;height:25px;border:1px solid #bbb;border-radius:4px;box-shadow:1px 1px 2px rgba(0,0,0,.15);font-size:11px;color:var(--blue);text-align:center;line-height:23px;background:#fff}
.feature .btn{margin-top:11px}

/* welcome + services */
.section-title{font-family:Tinos,Georgia,serif;font-style:italic;font-weight:400;font-size:14px;color:#333}
.section-title b{color:var(--blue);font-weight:700}
.welcome{left:75px;top:737px;width:370px}
.welcome p{margin-top:9px;font-size:12px;line-height:20px;letter-spacing:.2px}
.welcome .btn{margin-top:13px}
.services{left:465px;top:737px;width:180px}
.services ul{list-style:none;margin-top:6px}
.services li{display:flex;align-items:center;gap:9px;font-size:11.5px;height:24.3px}
.services .btn{margin-top:9px}

/* clients */
.clients{left:73px;top:958px;width:580px;height:156px;border:1px solid var(--line);border-radius:4px;box-shadow:0 1px 4px rgba(0,0,0,.2)}
.clients .section-title{position:absolute;left:11px;top:8px}
.clients .rule{position:absolute;left:10px;right:14px;top:31px;border-top:1px solid var(--line)}
.clients .arrows{position:absolute;right:17px;top:8px;display:flex;gap:4px}
.client{position:absolute;top:42px;width:126px}
.client .photo{height:75px;border:1px solid #bbb;background:linear-gradient(135deg,#cdb7a4,#e9dfd5 55%,#a9a59f)}
.client p{font-family:Tinos,Georgia,serif;font-style:italic;font-size:11px;margin-top:10px;padding-left:3px}

/* footer */
.footer{left:0;top:1133px;width:722px;height:67px;background:var(--foot);border-top:1px solid #ddd}
.footer .org{position:absolute;left:77px;top:6px;font-size:12px;font-weight:700;font-style:italic;color:#777;text-decoration:underline;line-height:15px}
.footer .contact{position:absolute;left:77px;top:21px;font-size:9px;line-height:11px;color:var(--faint)}
.footer .find{position:absolute;left:530px;top:19px;font-size:9px;color:var(--muted);display:flex;align-items:center;gap:6px}
.footer .find i{width:12px;height:12px;border-radius:2px;background:#2d6fb5;display:inline-block}
.footer .copy{position:absolute;left:515px;top:38px;font-size:9px;color:var(--muted)}
</style>
</head>
<body>

<header>
  <div class="abs brand">velorahelp</div>
  <div class="abs call">Call us @ 1800 - 55 - 307418</div>
  <div class="abs search">search...
    <svg width="12" height="12" viewBox="0 0 12 12"><circle cx="5" cy="5" r="3.5" fill="none" stroke="#888" stroke-width="1.5"/><line x1="7.5" y1="7.5" x2="11" y2="11" stroke="#888" stroke-width="2"/></svg>
  </div>
  <nav class="abs nav">
    <span class="current" style="left:30px">Home</span>
    <span style="left:110px;color:#555">|</span>
    <span style="left:158px">About Us</span>
    <span style="left:262px;color:#555">|</span>
    <span style="left:310px">Our Services</span>
    <span style="left:438px;color:#555">|</span>
    <span style="left:481px">Contact Us</span>
  </nav>
</header>

<div class="abs hero" role="img" aria-label="Photo of three lab researchers in white coats gathered around a microscope"></div>
<div class="abs dots"><i></i><i></i><i></i><i></i></div>

<section>
  <div class="abs feature" style="left:74px">
    <h3>Recieving calls</h3>
    <div class="photo" role="img" aria-label="Photo of a call-centre agent wearing a headset" style="background:linear-gradient(120deg,#8a8f6a,#d8cdb5 60%,#f1ece4)"></div>
    <p>Put here something about collection of client query or calls to researching over them in a brief.</p>
    <span class="btn">More</span>
  </div>
  <div class="abs feature" style="left:273px">
    <h3>Reserching Issues</h3>
    <div class="photo" role="img" aria-label="Photo of a man at a desk with two computer monitors" style="background:linear-gradient(120deg,#5d6f5a,#a9b6c3 50%,#7e8795)"></div>
    <p>Put here something about researching of client query or calls to researching over them in a brief.</p>
    <span class="btn">More</span>
  </div>
  <div class="abs feature" style="left:471px">
    <h3>Resolving Problems</h3>
    <div class="photo" role="img" aria-label="Photo of two business people shaking hands" style="background:linear-gradient(180deg,#c9dbee,#9fbfe0 55%,#e6eef7)"></div>
    <p>Put here something about resolving of client query or calls to researching over them in a brief.</p>
    <span class="btn">More</span>
  </div>
</section>

<section class="abs welcome">
  <h2 class="section-title"><b>Welcome</b> to our site</h2>
  <p>It is a virtual assistance/concierge company that helps the busy professional by remotely providing administrative, technical and/or creative business support services, specializing in the medical device industry. Company name is velorahelp. It is a virtual assistance/concierge company that helps the busy professional by remotely providing administrative, technical and/or creative business support services.</p>
  <span class="btn">More</span>
</section>

<section class="abs services">
  <h2 class="section-title"><b>Our</b> Services</h2>
  <ul>
    <li><svg width="15" height="15" viewBox="0 0 15 15"><circle cx="7.5" cy="7.5" r="6.5" fill="#f4f4f4" stroke="#bbb"/><path d="M6 4.5 L10 7.5 L6 10.5Z" fill="#2a7cc0"/></svg>Service goes here</li>
    <li><svg width="15" height="15" viewBox="0 0 15 15"><circle cx="7.5" cy="7.5" r="6.5" fill="#f4f4f4" stroke="#bbb"/><path d="M6 4.5 L10 7.5 L6 10.5Z" fill="#2a7cc0"/></svg>Service goes here</li>
    <li><svg width="15" height="15" viewBox="0 0 15 15"><circle cx="7.5" cy="7.5" r="6.5" fill="#f4f4f4" stroke="#bbb"/><path d="M6 4.5 L10 7.5 L6 10.5Z" fill="#2a7cc0"/></svg>Service goes here</li>
    <li><svg width="15" height="15" viewBox="0 0 15 15"><circle cx="7.5" cy="7.5" r="6.5" fill="#f4f4f4" stroke="#bbb"/><path d="M6 4.5 L10 7.5 L6 10.5Z" fill="#2a7cc0"/></svg>Service goes here</li>
    <li><svg width="15" height="15" viewBox="0 0 15 15"><circle cx="7.5" cy="7.5" r="6.5" fill="#f4f4f4" stroke="#bbb"/><path d="M6 4.5 L10 7.5 L6 10.5Z" fill="#2a7cc0"/></svg>Service goes here</li>
    <li><svg width="15" height="15" viewBox="0 0 15 15"><circle cx="7.5" cy="7.5" r="6.5" fill="#f4f4f4" stroke="#bbb"/><path d="M6 4.5 L10 7.5 L6 10.5Z" fill="#2a7cc0"/></svg>Service goes here</li>
  </ul>
  <span class="btn">More</span>
</section>

<section class="abs clients">
  <h2 class="section-title"><b>Our</b> Clients</h2>
  <div class="arrows">
    <svg width="15" height="15" viewBox="0 0 15 15"><circle cx="7.5" cy="7.5" r="6.5" fill="#f4f4f4" stroke="#bbb"/><path d="M9 4.5 L5 7.5 L9 10.5Z" fill="#2a7cc0"/></svg>
    <svg width="15" height="15" viewBox="0 0 15 15"><circle cx="7.5" cy="7.5" r="6.5" fill="#f4f4f4" stroke="#bbb"/><path d="M6 4.5 L10 7.5 L6 10.5Z" fill="#2a7cc0"/></svg>
  </div>
  <div class="rule"></div>
  <div class="client" style="left:10px"><div class="photo" role="img" aria-label="Client portrait photo"></div><p>Maple Grove Clinic</p></div>
  <div class="client" style="left:154px"><div class="photo" role="img" aria-label="Client portrait photo"></div><p>Maple Grove Clinic</p></div>
  <div class="client" style="left:298px"><div class="photo" role="img" aria-label="Client portrait photo"></div><p>Maple Grove Clinic</p></div>
  <div class="client" style="left:439px"><div class="photo" role="img" aria-label="Client portrait photo"></div><p>Maple Grove Clinic</p></div>
</section>

<footer class="abs footer">
  <div class="org">velorahelp</div>
  <div class="contact">Emergency Call : 1800-00-0417<br>Fax : 6510093872<br>E-mail : help4@velorahelp.example</div>
  <div class="find">Find Us : <i role="img" aria-label="Social link"></i><i role="img" aria-label="Social link"></i><i role="img" aria-label="Social link"></i></div>
  <div class="copy">Copyright 2012 | Privacy Policy</div>
</footer>

</body>
</html>
```